The Harrowgate

We need a APP for our members. this is a Private Bar/Venue. history of the brick building is it was built in1898 and was a gentleman club, oyster house, cigar factory and then law offices before we purchased and are beginning restoration.
the APP must include
1. direct texting to the concierge
2. calendar of events
3. Pellmont Lock To open the lock, anyone with a code can approach the door, enable their phone's Bluetooth and press the relevant address from the app.
Read more: http://www.brevinpost.example/tech/article-5521840/keyless-entry-phone-door-lock-explained.html#qq7rTb2mWx
4. Menus from various restaurants from our surrounding area
5. member name and member number to give the feel that the app is personalized
6. the members account balance
7. ability to pay their bill with credit card or pim coin monthly and automatically.
8. link to zirva with its own icon within the app.
9.the ability to reserve the room
Anything else that may of interest for our members that may be relevant that I may not have mentioned since we are new at this...
35 to 60 years of age
Club
Designer to choose colors to be used in the design.

```html
<!DOCTYPE html>
<html lang="en">
<head>
<meta charset="utf-8">
<title>The Harrowgate – Concierge</title>
<link href="https://fonts.googleapis.com/css2?family=Montserrat:wght@300;400;500;600;700&family=Mulish:wght@400;700&display=swap" rel="stylesheet">
<style>
  :root {
    --page: #e4e8f0;
    --white: #ffffff;
    --ink: #111111;
    --screen: #000000;
    --panel: #1c1c1c;
    --line: #2a2a2a;
    --tan: #b08d78;
    --tan-text: #b9947c;
    --accent: #c07850;
    --muted: #3a3a3a;
    --icon: #4a4a4a;
    --light: #f2f2f2;
  }
  * { margin: 0; padding: 0; box-sizing: border-box; }
  html, body { width: 800px; height: 1200px; overflow: hidden; }
  body { background: var(--page); font-family: "Mulish", sans-serif; position: relative; }

  .showcase-bar { position: absolute; left: 0; top: 0; width: 800px; height: 64px; background: var(--white); }
  .showcase-title { position: absolute; left: 18px; top: 17px; font: 500 25px "Montserrat", sans-serif; color: var(--ink); }
  .showcase-count { position: absolute; right: 18px; top: 25px; font: 400 18px "Montserrat", sans-serif; color: var(--ink); }

  .app { position: absolute; left: 100px; top: 92px; width: 600px; height: 1066px; background: var(--screen); overflow: hidden; color: var(--light); }
  .abs { position: absolute; }

  .status { font: 400 17px "Mulish", sans-serif; color: #ddd; top: 8px; }
  .nav-line, .divider { position: absolute; left: 0; width: 600px; height: 1px; background: var(--line); }

  .nav-title { left: 0; width: 600px; top: 55px; text-align: center; font: 300 24px "Montserrat", sans-serif; letter-spacing: 7px; color: #fff; }

  .venue-category { left: 26px; top: 130px; font: 400 19px "Montserrat", sans-serif; letter-spacing: 1.5px; color: var(--tan-text); }
  .venue-name { left: 24px; top: 157px; font: 600 44px "Montserrat", sans-serif; letter-spacing: 4px; color: #fff; }
  .venue-change { left: 448px; top: 158px; font: 400 23px "Montserrat", sans-serif; letter-spacing: 2px; color: var(--tan-text); }

  .avatar { position: absolute; border-radius: 50%; }
  .avatar-venue { width: 56px; height: 56px; left: 24px; background: radial-gradient(circle at 50% 55%, #8a5a22, #2a1a0c 70%); }
  .avatar-member { width: 27px; height: 27px; left: 550px; background: radial-gradient(circle at 50% 45%, #d8d8d8, #7a7a7a); }

  .bubble { position: absolute; font: 400 26px/32px "Mulish", sans-serif; }
  .bubble-venue { background: var(--tan); color: #1a1a1a; border-radius: 28px; }
  .bubble-member { background: var(--panel); color: #f4f4f4; border-radius: 28px 28px 4px 28px; }
  .bubble-text { padding: 12px 24px; }
  .bubble-action { border-top: 1px solid #8c6e5c; text-align: center; font-weight: 700; height: 70px; line-height: 70px; }

  .composer-placeholder { left: 26px; top: 880px; font: 400 23px "Mulish", sans-serif; color: var(--muted); }
  .composer-tools { left: 0; top: 932px; width: 600px; height: 44px; }

  .tab { position: absolute; top: 1000px; width: 150px; text-align: center; }
  .tab-label { position: absolute; top: 40px; left: 0; width: 150px; font: 400 15px "Montserrat", sans-serif; letter-spacing: 0.5px; color: #555; }
  .tab-active .tab-label { color: #fff; }
</style>
</head>
<body>
  <header class="showcase-bar">
    <div class="showcase-title">The Harrowgate</div>
    <div class="showcase-count">5 Screens</div>
  </header>

  <main class="app">
    <div class="abs status" style="left:12px;">●●●○○ Carrier
      <svg width="20" height="14" viewBox="0 0 20 14" style="vertical-align:-1px"><path d="M2 5a11 11 0 0 1 16 0M5 8a7 7 0 0 1 10 0M8 11a3 3 0 0 1 4 0" stroke="#ddd" stroke-width="2" fill="none" stroke-linecap="round"/></svg>
    </div>
    <div class="abs status" style="left:0;width:600px;text-align:center;">3:24 PM</div>
    <div class="abs status" style="left:500px;">100%
      <svg width="38" height="16" viewBox="0 0 38 16" style="vertical-align:-2px"><rect x="1" y="1" width="33" height="14" rx="2" fill="#fff" stroke="#ddd"/><rect x="35" y="5" width="2" height="6" fill="#ddd"/></svg>
    </div>

    <svg class="abs" style="left:24px;top:54px" width="30" height="26" viewBox="0 0 30 26"><path d="M0 2h30M0 13h30M0 24h30" stroke="#fff" stroke-width="3"/></svg>
    <div class="abs nav-title">CONCIERGE</div>
    <div class="nav-line" style="top:102px"></div>

    <section class="venue-header">
      <div class="abs venue-category">Bar &amp; Restaurants</div>
      <div class="abs venue-name">Quernova</div>
      <div class="abs venue-change">Change
        <svg width="18" height="12" viewBox="0 0 18 12" style="margin-left:6px"><path d="M2 3l7 7 7-7" stroke="#b9947c" stroke-width="2" fill="none"/></svg>
      </div>
    </section>
    <div class="divider" style="top:236px"></div>

    <section class="thread">
      <div class="avatar avatar-venue" style="top:263px" role="img" aria-label="Venue photo of the bar interior"></div>
      <div class="bubble bubble-venue" style="left:93px;top:263px;width:335px;height:56px;"><div class="bubble-text">Sure! I can help you out.</div></div>

      <div class="bubble bubble-member" style="left:460px;top:356px;width:85px;height:56px;"><div class="bubble-text" style="text-align:center;padding:12px 0;">OK</div></div>
      <div class="avatar avatar-member" style="top:386px" role="img" aria-label="Member profile photo"></div>

      <div class="bubble bubble-member" style="left:178px;top:426px;width:367px;height:162px;"><div class="bubble-text" style="padding:13px 20px;width:322px;">Do you have a drink or recommended menus ?<br>I came with friends and boss.</div></div>
      <div class="avatar avatar-member" style="top:562px" role="img" aria-label="Member profile photo"></div>

      <div class="avatar avatar-venue" style="top:618px" role="img" aria-label="Venue photo of the bar interior"></div>
      <div class="bubble bubble-venue" style="left:93px;top:618px;width:405px;height:199px;">
        <div class="bubble-text" style="height:128px;padding:16px 24px;">Hi Jack! No problem, I have suggestion menus as follow, Please tap to see them.</div>
        <div class="bubble-action">See our popular menus</div>
      </div>
    </section>

    <div class="divider" style="top:858px"></div>
    <div class="abs composer-placeholder">Type a message...</div>
    <svg class="abs composer-tools" viewBox="0 0 600 44" fill="none" stroke="var(--icon)" stroke-width="2">
      <text x="18" y="35" font-family="Mulish, sans-serif" font-size="34" fill="#c07850" stroke="none">Aa</text>
      <rect x="92" y="10" width="36" height="26" rx="3"/><circle cx="110" cy="23" r="8"/><path d="M100 10l4-5h12l4 5"/>
      <rect x="168" y="8" width="30" height="30" rx="2" transform="rotate(-8 183 23)"/><path d="M172 32l8-9 6 6 4-4 6 6"/>
      <circle cx="255" cy="23" r="17"/><circle cx="249" cy="19" r="1.5"/><circle cx="261" cy="19" r="1.5"/><path d="M247 27q8 7 16 0"/>
      <rect x="308" y="6" width="40" height="34" rx="6"/>
      <text x="315" y="31" font-family="Mulish, sans-serif" font-size="17" fill="#4a4a4a" stroke="none">GIF</text>
      <rect x="394" y="4" width="14" height="24" rx="7"/><path d="M388 22a13 13 0 0 0 26 0M401 35v7M395 42h12"/>
      <rect x="454" y="8" width="38" height="28" rx="3"/><circle cx="464" cy="22" r="2.5"/><circle cx="473" cy="22" r="2.5"/><circle cx="482" cy="22" r="2.5"/>
    </svg>

    <div class="divider" style="top:988px"></div>
    <nav>
      <div class="tab" style="left:0">
        <svg width="150" height="36" viewBox="0 0 150 36" fill="none" stroke="#555" stroke-width="2"><path d="M60 2h12l-1 12a5 5 0 0 1-10 0zM66 19v15M61 34h10M78 2v32M78 2c6 2 6 12 0 14M84 2v10q0 4 2 4t2-4V2M86 16v18"/></svg>
        <div class="tab-label">Restaurants</div>
      </div>
      <div class="tab tab-active" style="left:151px">
        <svg width="150" height="36" viewBox="0 0 150 36"><path d="M75 2v6M62 6l4 4M88 6l-4 4" stroke="#fff" stroke-width="2"/><path d="M59 28a16 16 0 0 1 32 0z" fill="#fff"/><rect x="57" y="29" width="36" height="3" fill="#fff"/></svg>
        <div class="tab-label">Concierge</div>
      </div>
      <div class="tab" style="left:299px">
        <svg width="150" height="36" viewBox="0 0 150 36" fill="none" stroke="#555" stroke-width="2"><rect x="58" y="2" width="34" height="32"/><path d="M58 10h34M58 18h34M58 26h34M67 10v24M75 10v24M83 10v24"/></svg>
        <div class="tab-label">Calendar</div>
      </div>
      <div class="tab" style="left:450px">
        <svg width="150" height="36" viewBox="0 0 150 36" fill="none" stroke="#555" stroke-width="2"><circle cx="83" cy="12" r="9"/><circle cx="85" cy="10" r="2"/><path d="M77 19L60 34M64 30l3 3M68 27l3 3"/></svg>
        <div class="tab-label">Pellmont Locks</div>
      </div>
    </nav>
  </main>
</body>
</html>
```